Business card design for a dynamic IT consulting company

We need a business card design for a young firm, specialized in the Telecommunications/Consulting industry. The name of the company is Quindor and Partners Business Consulting Ltd. (Short name: Quindor and Partnes)
Quindor = solve read reverse, so we aim to be uncomplicated and solution-oriented. The small pipe in our logo is also related to the word solve. So we need a new business card design, which is simple, eye catching and something non traditional (I would probably prefer a square shaped design rather than a rectangle, but open for suggestions). Attached our logo.

Target Market(s)

Usually our customers are Tier1 Telecoms providers (Q-Netra, Palorix, etc) and their executives.

Industry/Entity Type

Business

Contact Information for Business Card

Name: Bence Tolnavari
Email: b.tolnavari@quindor.hu
Web: www.quindor.hu
Mobile: +36 30 518 2769
Title: Managing Director

Optional:
Company name: Quindor and Partners Ltd.
Address: 1087 Budapest, Tolvenka str. 28/C, Hungary

Font styles to use
Other font styles liked:
• helveticaneue_medium, Prime Regular are used now.

Colors

Designer to choose colors to be used in the design.

Requirements
Must have
• I would like to have a 2 sided design.
Nice to have
• I thought if we make the logo a bit bigger (without the company name), that could go to the back with the company name below. I though, if the pipe in the logo is somehow touchable on the business card, would be nice and unique.

```html
<!DOCTYPE html>
<html lang="en">
<head>
<meta charset="utf-8">
<title>Quindor and Partners – Business Card</title>
<link rel="stylesheet" href="https://fonts.googleapis.com/css2?family=Arimo:wght@400;700&display=swap">
<style>
  :root {
    --backdrop: #e2e2e2;
    --card: #f7f7f7;
    --band: #58595b;
    --ink: #555557;
    --ink-soft: #6a6a6c;
    --accent: #1a9ad6;
    --tint-pink: #eccde0;
    --tint-blue: #cfe6f3;
    --tint-grey: #dcdcdc;
  }
  * { margin: 0; padding: 0; box-sizing: border-box; }
  html, body {
    width: 1200px; height: 960px; overflow: hidden;
    background: var(--backdrop);
    font-family: "Arimo", Arial, sans-serif;
  }
  .card {
    position: absolute; top: 305px;
    width: 343px; height: 343px;
    background: var(--card);
    box-shadow: 0 0 0 1px rgba(0,0,0,0.06);
  }
  .card--front { left: 200px; }
  .card--back { left: 651px; }

  .side-band {
    position: absolute; left: 0; top: 0;
    width: 32px; height: 100%;
    background: var(--band);
  }
  .brand {
    position: absolute; display: flex; align-items: center;
    color: var(--ink); font-weight: 400; white-space: nowrap;
  }
  .brand__square {
    background: var(--accent); display: block;
  }
  .card--front .brand { left: 50px; top: 56px; font-size: 25px; gap: 10px; }
  .card--front .brand__square { width: 12px; height: 12px; }

  .contact { position: absolute; left: 68px; top: 135px; color: var(--ink-soft); }
  .contact__name {
    color: var(--accent); font-weight: 700; font-size: 19px;
    letter-spacing: 0.2px; text-transform: uppercase;
  }
  .contact__title { font-size: 15px; text-transform: uppercase; margin-top: 3px; letter-spacing: 0.2px; }
  .contact__address { font-size: 14px; line-height: 18px; margin-top: 14px; font-style: normal; }
  .contact__lines { list-style: none; margin-top: 12px; font-size: 14px; line-height: 18px; }
  .contact__lines li { display: flex; align-items: center; gap: 7px; }
  .contact__icon { width: 12px; height: 12px; flex: none; }

  .card--back .brand {
    left: 0; right: 0; top: 28px; justify-content: center; font-size: 33px; gap: 10px;
  }
  .card--back .brand__square { width: 10px; height: 10px; }
  .web {
    position: absolute; left: 0; right: 0; top: 74px;
    text-align: center; color: var(--ink); font-size: 14px; letter-spacing: 8.4px;
  }
  .pattern-field {
    position: absolute; left: 30px; top: 110px; width: 278px; height: 212px;
    background: linear-gradient(135deg, var(--tint-pink) 0%, var(--tint-blue) 45%, var(--tint-grey) 75%, var(--tint-blue) 100%);
    opacity: 0.75;
  }
</style>
</head>
<body>
  <section class="card card--front" aria-label="Card front">
    <div class="side-band"></div>
    <div class="brand"><span class="brand__square"></span>Quindor &amp; Partners</div>
    <div class="contact">
      <h1 class="contact__name">Bence Tolnavari</h1>
      <p class="contact__title">Managing Director</p>
      <address class="contact__address">
        Quindor and Partners Ltd.<br>
        1087 Budapest<br>
        Tolvenka str. 28/C, Hungary
      </address>
      <ul class="contact__lines">
        <li>
          <svg class="contact__icon" viewBox="0 0 12 12" aria-hidden="true">
            <rect x="3" y="0.5" width="6" height="11" rx="1.2" fill="none" stroke="#1a9ad6" stroke-width="1.2"/>
            <circle cx="6" cy="9.6" r="0.7" fill="#1a9ad6"/>
          </svg>
          +36 30 518 2769
        </li>
        <li>
          <svg class="contact__icon" viewBox="0 0 12 12" aria-hidden="true">
            <rect x="0.5" y="2.5" width="11" height="7.5" fill="#1a9ad6"/>
            <path d="M0.5 2.5 L6 7 L11.5 2.5" fill="none" stroke="#f7f7f7" stroke-width="1"/>
          </svg>
          b.tolnavari@quindor.hu
        </li>
      </ul>
    </div>
  </section>

  <section class="card card--back" aria-label="Card back">
    <div class="brand"><span class="brand__square"></span>Quindor &amp; Partners</div>
    <p class="web">www.quindor.hu</p>
    <div class="pattern-field" role="img" aria-label="Faint enlarged brand symbol pattern in pale pink, blue and grey"></div>
  </section>
</body>
</html>
```